Business Card Design

We need a business card designed for our new company. Prefer a black card with white logo & writing.

Contact Information for Business Card

Ted Galloway, address: 7-4812 Fernhollow Road, Abbotsford, BC, V3K 8R2, Office Phone: 604-712-3390, Cell: 604-947-2164, Email: ted@resinworkshub.ca

Colors

Designer to choose only greyscale colors for use in the design.

```html
<!DOCTYPE html>
<html lang="en">
<head>
<meta charset="utf-8">
<title>Resinworks Hub — Business Card</title>
<link rel="stylesheet" href="https://fonts.googleapis.com/css2?family=Montserrat:wght@400;600;800&display=swap">
<style>
  :root {
    --backdrop: #a9a5a5;
    --card-black: #1f1f1f;
    --card-black-edge: #2e2e2e;
    --card-white: #ffffff;
    --ink: #111111;
    --ink-soft: #333333;
    --paper-text: #f4f4f4;
  }
  * { box-sizing: border-box; margin: 0; padding: 0; }
  html, body { width: 1200px; height: 900px; overflow: hidden; }
  body {
    background: var(--backdrop);
    font-family: "Montserrat", sans-serif;
    position: relative;
  }
  .card {
    position: absolute;
    width: 560px;
    height: 320px;
    border-radius: 22px;
    box-shadow: 0 14px 30px rgba(0,0,0,0.25);
  }
  .card-front {
    left: 90px;
    top: 100px;
    background: linear-gradient(135deg, var(--card-black-edge), var(--card-black) 60%);
    display: flex;
    align-items: center;
    justify-content: center;
  }
  .brand {
    font-weight: 800;
    text-transform: uppercase;
    letter-spacing: 1px;
    line-height: 1;
  }
  .card-front .brand {
    color: var(--paper-text);
    font-size: 40px;
  }
  .card-back {
    left: 550px;
    top: 480px;
    background: var(--card-white);
    color: var(--ink);
  }
  .card-back .brand {
    position: absolute;
    right: 34px;
    top: 34px;
    font-size: 22px;
    color: var(--ink);
  }
  .person {
    position: absolute;
    left: 34px;
    top: 110px;
  }
  .person-name { font-weight: 800; font-size: 22px; }
  .person-role { font-weight: 400; font-size: 13px; color: var(--ink-soft); margin-top: 4px; }
  .address {
    position: absolute;
    right: 34px;
    top: 112px;
    text-align: right;
    font-size: 13px;
    line-height: 1.45;
    color: var(--ink-soft);
  }
  .contacts {
    position: absolute;
    left: 34px;
    bottom: 30px;
    list-style: none;
    font-size: 14px;
    color: var(--ink-soft);
  }
  .contacts li {
    display: flex;
    align-items: center;
    gap: 12px;
    margin-top: 6px;
  }
  .contacts svg { width: 14px; height: 14px; fill: var(--ink); flex: none; }
</style>
</head>
<body>
  <section class="card card-front">
    <span class="brand">Resinworks Hub</span>
  </section>

  <section class="card card-back">
    <span class="brand">Resinworks Hub</span>
    <div class="person">
      <p class="person-name">Ted Galloway</p>
      <p class="person-role">owner</p>
    </div>
    <p class="address">7-4812 Fernhollow Road,<br>Abbotsford, BC, V3K 8R2</p>
    <ul class="contacts">
      <li>
        <svg viewBox="0 0 24 24" aria-hidden="true"><path d="M6.6 10.8a15.1 15.1 0 0 0 6.6 6.6l2.2-2.2c.3-.3.7-.4 1-.2 1.1.4 2.3.6 3.6.6.6 0 1 .4 1 1V20c0 .6-.4 1-1 1A17 17 0 0 1 3 4c0-.6.4-1 1-1h3.5c.6 0 1 .4 1 1 0 1.3.2 2.5.6 3.6.1.3 0 .7-.2 1z"/></svg>
        <span>604-712-3390</span>
      </li>
      <li>
        <svg viewBox="0 0 24 24" aria-hidden="true"><path d="M7 1h10a2 2 0 0 1 2 2v18a2 2 0 0 1-2 2H7a2 2 0 0 1-2-2V3a2 2 0 0 1 2-2zm0 3v14h10V4zm5 15.2a1 1 0 1 0 0 2 1 1 0 0 0 0-2z"/></svg>
        <span>604-947-2164</span>
      </li>
      <li>
        <svg viewBox="0 0 24 24" aria-hidden="true"><path d="M2 5h20v14H2zm2 2v.5l8 5 8-5V7zm0 2.9V17h16V9.9l-8 5z"/></svg>
        <span>ted@resinworkshub.ca</span>
      </li>
      <li>
        <svg viewBox="0 0 24 24" aria-hidden="true"><path d="M12 2a10 10 0 1 0 0 20 10 10 0 0 0 0-20zm6.9 9h-3a15 15 0 0 0-1.3-5.6A8 8 0 0 1 18.9 11zM12 4.1c.9 1.2 1.8 3.6 1.9 6.9h-3.8c.1-3.3 1-5.7 1.9-6.9zM9.4 5.4A15 15 0 0 0 8.1 11h-3a8 8 0 0 1 4.3-5.6zM5.1 13h3a15 15 0 0 0 1.3 5.6A8 8 0 0 1 5.1 13zm6.9 6.9c-.9-1.2-1.8-3.6-1.9-6.9h3.8c-.1 3.3-1 5.7-1.9 6.9zm2.6-1.3a15 15 0 0 0 1.3-5.6h3a8 8 0 0 1-4.3 5.6z"/></svg>
        <span>www.resinworkshub.ca</span>
      </li>
    </ul>
  </section>
</body>
</html>
```